Harborlight Amusement Collective (HAC)

We need a business card design for Harborlight Amusement Collective. Modern and sleek looking, with all critical information. Open to single or double sided designs, if double sided info needs to be all on one side. The main Logo is Harborlight Amusement collective and must be on the card. The other three logos are for the brands that fall under the group, they might be good on the back.

Industry/Entity Type

Business

```html
<!DOCTYPE html>
<html lang="en">
<head>
<meta charset="utf-8">
<title>Harborlight Amusement Collective – Business Card</title>
<link href="https://fonts.googleapis.com/css2?family=Montserrat:wght@400;500;600;700&family=Roboto+Condensed:wght@700&display=swap" rel="stylesheet">
<style>
  :root {
    --backdrop: #e4e4e4;
    --brand-blue: #2457a0;
    --brand-green: #8aa83a;
    --paper: #ffffff;
    --ink: #222222;
  }
  * { box-sizing: border-box; margin: 0; padding: 0; }
  html, body { width: 1200px; height: 852px; overflow: hidden; }
  body {
    background: var(--backdrop);
    font-family: "Montserrat", Arial, sans-serif;
    position: relative;
  }
  .card {
    position: absolute;
    top: 276px;
    width: 520px;
    height: 300px;
    border-radius: 22px;
    overflow: hidden;
    background: var(--paper);
    box-shadow: 0 6px 18px rgba(0,0,0,.18);
  }
  .card--back { left: 60px; }
  .card--front { left: 620px; }

  /* Back side */
  .back__field {
    position: absolute; inset: 0 0 92px 0;
    background: var(--brand-blue);
    display: flex; flex-direction: column; align-items: center; justify-content: center;
    color: var(--paper);
  }
  .brand-mark {
    width: 52px; height: 52px; border: 4px solid var(--paper); margin-bottom: 16px;
  }
  .wordmark {
    font-weight: 700; letter-spacing: .5px; text-transform: uppercase; text-align: center;
  }
  .back__field .wordmark { font-size: 19px; line-height: 1.3; }
  .wordmark__rule {
    display: flex; align-items: center; gap: 12px; font-size: 15px; letter-spacing: 8px;
  }
  .wordmark__rule::before, .wordmark__rule::after {
    content: ""; width: 70px; height: 2px; background: currentColor;
  }
  .sub-brands {
    position: absolute; left: 0; right: 0; bottom: 36px; height: 56px;
    display: flex; align-items: center; justify-content: space-evenly;
  }
  .sub-brand {
    display: flex; align-items: center; gap: 7px;
    font-weight: 700; font-size: 15px; color: var(--brand-blue);
  }
  .sub-brand__dot { width: 16px; height: 16px; border-radius: 50%; background: var(--brand-green); }
  .sub-brands__divider { width: 1px; height: 30px; background: #9aa; }
  .back__web {
    position: absolute; left: 0; right: 0; bottom: 10px;
    display: flex; align-items: center; justify-content: center; gap: 14px;
    font-size: 12px; color: var(--brand-blue); font-weight: 500;
  }
  .back__web::before, .back__web::after {
    content: ""; width: 50px; height: 2px; background: var(--brand-green);
  }

  /* Front side */
  .front__band { position: absolute; inset: 0; }
  .front__wordmark {
    position: absolute; left: 26px; top: 46px; color: var(--brand-blue);
  }
  .front__wordmark .wordmark { font-size: 17px; text-align: left; line-height: 1.3; }
  .front__wordmark .wordmark__rule { font-size: 14px; letter-spacing: 7px; }
  .front__wordmark .wordmark__rule::before, .front__wordmark .wordmark__rule::after { width: 60px; }
  .front__mark {
    position: absolute; left: 392px; top: 58px; width: 96px; height: 96px;
    background: var(--brand-blue); border: 6px solid var(--paper);
    box-shadow: 0 0 0 3px var(--brand-blue);
  }
  .contact {
    position: absolute; left: 26px; top: 168px; color: var(--paper);
  }
  .contact__name {
    font-family: "Roboto Condensed", Arial, sans-serif; font-weight: 700; font-size: 19px;
  }
  .contact__role { font-size: 11px; margin-bottom: 6px; }
  .contact__list { list-style: none; font-size: 11px; line-height: 1.5; }
  .contact__list li { display: flex; align-items: center; gap: 8px; }
  .contact__list svg { width: 11px; height: 11px; fill: var(--paper); }
  .front__address {
    position: absolute; left: 26px; bottom: 14px; font-size: 12px; color: var(--ink); font-weight: 500;
  }
</style>
</head>
<body>

<section class="card card--back" aria-label="Card back">
  <div class="back__field">
    <div class="brand-mark"></div>
    <div class="wordmark">
      Harborlight Amusement
      <div class="wordmark__rule">Collective</div>
    </div>
  </div>
  <div class="sub-brands">
    <span class="sub-brand"><span class="sub-brand__dot"></span>HarborPass</span>
    <span class="sub-brands__divider"></span>
    <span class="sub-brand"><span class="sub-brand__dot"></span>Boardwalk Hosting</span>
    <span class="sub-brands__divider"></span>
    <span class="sub-brand"><span class="sub-brand__dot"></span>gatestub</span>
  </div>
  <div class="back__web">www.harborlightcollective.com</div>
</section>

<section class="card card--front" aria-label="Card front">
  <svg class="front__band" viewBox="0 0 520 300" preserveAspectRatio="none" aria-hidden="true">
    <polygon points="0,160 170,160 400,50 520,50 520,258 0,258" fill="var(--brand-blue)"/>
  </svg>
  <div class="front__wordmark">
    <div class="wordmark">
      Harborlight Amusement
      <div class="wordmark__rule">Collective</div>
    </div>
  </div>
  <div class="front__mark"></div>
  <div class="contact">
    <div class="contact__name">Morgan Ellis Reed</div>
    <div class="contact__role">Managing Director</div>
    <ul class="contact__list">
      <li><svg viewBox="0 0 12 12"><path d="M2 1h2l1 3-1.5 1a7 7 0 0 0 3.5 3.5L8 7l3 1v2a1 1 0 0 1-1 1A9 9 0 0 1 1 2a1 1 0 0 1 1-1z"/></svg>555.010.2040</li>
      <li><svg viewBox="0 0 12 12"><path d="M1 2h10v8H1zM1.8 2.8 6 6.5l4.2-3.7" stroke="#2457a0" stroke-width="1"/></svg>mreed@harborlightcollective.com</li>
      <li><svg viewBox="0 0 12 12"><circle cx="6" cy="6" r="5"/><path d="M1 6h10M6 1c-3 3-3 7 0 10M6 1c3 3 3 7 0 10" stroke="#2457a0" stroke-width=".8" fill="none"/></svg>www.harborlightcollective.com</li>
    </ul>
  </div>
  <div class="front__address">18 Pier Lane, Saltmarsh Bay, US 40127</div>
</section>

</body>
</html>
```